Business Card for a Jewellery Brand

Business card for an upscale jewellery brand. Attached is the brand logo and icon and color board. I am looking for two card versions: one for the founder and one is generic. The card should be elegant and convey upscale and premium feel. I am open to both square and rectangle card shapes.

Industry/Entity Type

Jewelry

Contact Information for Business Card

Two cards: (1) Sunela Parvaniya (Founder) (2) General
(1) Sunela Parvaniya card should have Name: Sunela Parvaniya, Title: Founder Email id: sunela@quiremo.com.au. Phone no: +61452913307
(2) Generic card should have Email id: info@quiremo.com.au. Phone no: +61436207518

Requirements
Must have
• Workmark
• ICON
• Phone no
• Email ID
• ABN: 58219740312 (Note: ABN is Business number in Australia)
• Website: www.quiremo.com.au
• Instagram: quiremo_jewellery
• Facebook: @quiremojewellery
Nice to have
• Tagline

```html
<!DOCTYPE html>
<html lang="en">
<head>
<meta charset="utf-8">
<title>Quiremo Business Cards</title>
<link rel="stylesheet" href="https://fonts.googleapis.com/css2?family=Josefin+Sans:wght@300;400&family=Open+Sans:wght@400;700&display=swap">
<style>
  :root {
    --stage: #3a3230;
    --card: #161616;
    --card-edge: #0c0c0c;
    --pattern: #1f1f1f;
    --blush: #e8a5a0;
    --ink: #f2f2f2;
    --rule: #8a8a8a;
  }
  * { margin: 0; padding: 0; box-sizing: border-box; }
  html, body { width: 1200px; height: 864px; overflow: hidden; }
  body {
    background: var(--stage);
    position: relative;
    font-family: "Open Sans", sans-serif;
  }
  .card {
    position: absolute;
    width: 540px;
    height: 310px;
    background: var(--card);
    border-radius: 4px;
    box-shadow: 0 10px 24px rgba(0,0,0,.45);
    overflow: hidden;
  }
  /* back of card */
  .card-back { left: 60px; top: 90px; }
  .card-back .pattern-field {
    position: absolute; inset: 0;
    background: radial-gradient(ellipse at 50% 40%, #242424 0%, var(--pattern) 55%, var(--card) 100%);
  }
  .card-back .brand-name {
    position: absolute; left: 0; right: 0; top: 92px;
    text-align: center;
    font-family: "Josefin Sans", sans-serif;
    font-weight: 300;
    font-size: 44px;
    letter-spacing: 12px;
    color: #c9c9c9;
  }
  .card-back .tagline-row {
    position: absolute; left: 40px; right: 40px; top: 196px;
    display: flex; align-items: center; gap: 14px;
  }
  .card-back .tagline-row .line { flex: 1; height: 1px; background: var(--rule); }
  .card-back .tagline {
    font-family: "Josefin Sans", sans-serif;
    font-weight: 300;
    font-size: 13px;
    letter-spacing: 2px;
    color: #bdbdbd;
    text-transform: uppercase;
  }
  /* front of card */
  .card-front { left: 600px; top: 420px; }
  .card-front .wordmark {
    position: absolute; left: 30px; top: 0; width: 250px; height: 100%;
    display: flex; flex-direction: column; align-items: center; justify-content: center; gap: 18px;
  }
  .card-front .wordmark .mark-dot {
    width: 56px; height: 56px; border: 2px solid var(--blush);
  }
  .card-front .wordmark .brand-name {
    font-family: "Josefin Sans", sans-serif;
    font-weight: 300;
    font-size: 38px;
    letter-spacing: 8px;
    color: var(--blush);
  }
  .card-front .divider {
    position: absolute; left: 300px; top: 40px; width: 1px; height: 230px;
    background: linear-gradient(to bottom, transparent, #d8d8d8 30%, #d8d8d8 70%, transparent);
  }
  .card-front .details { position: absolute; left: 320px; top: 58px; color: var(--ink); }
  .person-name { color: var(--blush); font-weight: 700; font-size: 15px; }
  .person-role { font-size: 15px; margin-bottom: 6px; }
  .abn { font-size: 13px; margin-bottom: 8px; }
  .contact-list { list-style: none; }
  .contact-list li {
    display: flex; align-items: center; gap: 8px;
    font-size: 13px; line-height: 19px;
  }
  .contact-list .icon { width: 12px; height: 12px; flex: none; }
  .contact-list .social-box { width: 10px; height: 10px; background: var(--blush); border-radius: 2px; flex: none; margin: 0 1px; }
</style>
</head>
<body>

<section class="card card-back" aria-label="Card back">
  <div class="pattern-field" role="img" aria-label="Repeating dark geometric brand pattern"></div>
  <div class="brand-name">QUIREMO</div>
  <div class="tagline-row">
    <span class="line"></span>
    <span class="tagline">Love is in the air</span>
    <span class="line"></span>
  </div>
</section>

<section class="card card-front" aria-label="Card front">
  <div class="wordmark">
    <span class="mark-dot"></span>
    <span class="brand-name">QUIREMO</span>
  </div>
  <div class="divider"></div>
  <div class="details">
    <p class="person-name">Sunela Parvaniya</p>
    <p class="person-role">Founder</p>
    <p class="abn">ABN: 58219740312</p>
    <ul class="contact-list">
      <li>
        <svg class="icon" viewBox="0 0 12 12" aria-hidden="true"><rect x="3" y="0.5" width="6" height="11" rx="1" fill="none" stroke="#e8a5a0" stroke-width="1.2"/><circle cx="6" cy="9.6" r=".7" fill="#e8a5a0"/></svg>
        +61452913307
      </li>
      <li>
        <svg class="icon" viewBox="0 0 12 12" aria-hidden="true"><rect x=".6" y="2.5" width="10.8" height="7.5" fill="none" stroke="#e8a5a0" stroke-width="1.2"/><path d="M.8 3l5.2 4 5.2-4" fill="none" stroke="#e8a5a0" stroke-width="1.2"/></svg>
        sunela@quiremo.com.au
      </li>
      <li>
        <svg class="icon" viewBox="0 0 12 12" aria-hidden="true"><path d="M6 11.5C3 7.5 2 6 2 4.3a4 4 0 0 1 8 0C10 6 9 7.5 6 11.5z" fill="#e8a5a0"/><circle cx="6" cy="4.3" r="1.5" fill="#161616"/></svg>
        www.quiremo.com.au
      </li>
      <li><span class="social-box"></span>quiremo_jewellery</li>
      <li><span class="social-box"></span>@quiremojewellery</li>
    </ul>
  </div>
</section>

</body>
</html>
```